Tovarin Capital LLC

Need Professional Business cards for New Investment Fund

Target Market(s)

High Quality investors

Industry/Entity Type

Financial

Contact Information for Business Card

Phone Number +1 555 284 6190
Name Lukas Varenko
Title Fund Manager
email lv@FundTovarin.com
Website www.FundTovarin.com

Colors

Designer to choose colors to be used in the design.

Requirements
Must have
• Must have our Logo and all of the above. Must be made so lettering and loge can be raised

```html
<!DOCTYPE html>
<html lang="en">
<head>
<meta charset="utf-8">
<title>Tovarin Capital – Business Card</title>
<link rel="stylesheet" href="https://fonts.googleapis.com/css2?family=Montserrat:wght@400;500;600&family=Oswald:wght@500;600&display=swap">
<style>
  :root {
    --backdrop: #141414;
    --card: #1e1e1f;
    --card-edge: #262627;
    --silver: #c9c9c9;
    --silver-soft: #a9a9a9;
    --accent-green: #3fd43a;
  }
  * { margin: 0; padding: 0; box-sizing: border-box; }
  html, body {
    width: 1200px; height: 900px; overflow: hidden;
    background: var(--backdrop);
  }
  .canvas {
    position: relative; width: 1200px; height: 900px;
    display: flex; flex-direction: column; align-items: center; justify-content: center; gap: 30px;
  }
  .card {
    position: relative; width: 700px; height: 400px;
    background: var(--card);
    border: 1px solid var(--card-edge);
    box-shadow: 0 18px 40px rgba(0,0,0,.55);
  }
  /* front */
  .card-front { display: flex; align-items: center; justify-content: center; }
  .wordmark {
    display: flex; align-items: center; gap: 14px;
    font-family: "Montserrat", sans-serif; font-weight: 500;
    font-size: 40px; letter-spacing: 10px; color: var(--silver);
  }
  .wordmark-square { width: 16px; height: 16px; background: var(--silver); }
  /* back */
  .identity {
    position: absolute; right: 395px; top: 140px; text-align: right;
  }
  .person-name {
    font-family: "Oswald", sans-serif; font-weight: 600;
    font-size: 36px; letter-spacing: 2px; text-transform: uppercase;
    color: var(--silver); line-height: 1.1; white-space: nowrap;
  }
  .person-title {
    font-family: "Montserrat", sans-serif; font-weight: 400;
    font-size: 18px; letter-spacing: 1px; color: var(--silver-soft);
    margin-top: 2px;
  }
  .divider {
    position: absolute; left: 340px; top: 135px; width: 2px; height: 80px;
    background: var(--accent-green);
  }
  .contact-list {
    position: absolute; left: 372px; top: 138px; list-style: none;
    font-family: "Montserrat", sans-serif; font-size: 18px; letter-spacing: 1px;
    color: var(--silver); white-space: nowrap;
  }
  .contact-list li { display: flex; align-items: center; gap: 12px; height: 26px; }
  .contact-list svg { width: 14px; height: 14px; flex: none; }
  .address {
    position: absolute; left: 0; right: 0; bottom: 60px; text-align: center;
    font-family: "Montserrat", sans-serif; font-size: 19px; letter-spacing: 1.5px;
    color: var(--silver);
  }
</style>
</head>
<body>
<main class="canvas">
  <section class="card card-front" aria-label="Card front">
    <div class="wordmark"><span class="wordmark-square"></span>TOVARIN</div>
  </section>

  <section class="card card-back" aria-label="Card back">
    <div class="identity">
      <h1 class="person-name">Lukas Varenko</h1>
      <p class="person-title">Fund Manager</p>
    </div>
    <span class="divider"></span>
    <ul class="contact-list">
      <li>
        <svg viewBox="0 0 16 16" fill="none" stroke="#c9c9c9" stroke-width="1.4"><path d="M4 1.5l2.3 3-1.4 1.6c.8 1.8 2.2 3.2 4 4l1.6-1.4 3 2.3-1.2 2.5C7 13.5 2.5 9 1.5 2.7z"/></svg>
        +1 555 284 6190
      </li>
      <li>
        <svg viewBox="0 0 16 16" fill="none" stroke="#c9c9c9" stroke-width="1.4"><rect x="1.5" y="3.5" width="13" height="9"/><path d="M1.5 3.5l6.5 5 6.5-5"/></svg>
        lv@FundTovarin.com
      </li>
      <li>
        <svg viewBox="0 0 16 16" fill="none" stroke="#c9c9c9" stroke-width="1.2"><circle cx="8" cy="8" r="6.5"/><ellipse cx="8" cy="8" rx="3" ry="6.5"/><path d="M1.5 8h13M2.5 4.8h11M2.5 11.2h11"/></svg>
        www.FundTovarin.com
      </li>
    </ul>
    <p class="address">14 Marlow st. Eastbrook, NJ, 08990</p>
  </section>
</main>
</body>
</html>
```